Business Card for Polygraph business in Africa

Business Card . Polygraph Examiner based in Tanzania, East Africa.
Business Card will be used to disseminate contact information to potential clients.
It should convey that I am a professional specifically in the polygraph field and perform my work with integrity.

I have attached the business card that I'm currently using, which I threw together myself initially. It's not professional enough.

Target Market(s)

Banks, Accounting Firms, Government Ministries, Gas, Oil, & Gemstone Mining Concerns, Wildlife Conservation NGOs, International companies located in East Africa.

Industry/Entity Type

Business

Contact Information for Business Card

Veritrace Kilonga
Miriam Holloway
PO Box 48317
Arusha, Tanzania
+255 612 839 274
miriamholloway@postvale.example

Colors
00a990
f37122
faa54b

Requirements
Must have
• - Veritrace Kilonga (with the word "Polygraph" being more prominent than the word "Tanzania")
• - Forensic Examinations
• - Employment Screening
• - Should contain a logo of the Continental Truthline Society (of which I'm a member)
• - I would like an accent design (such as the polygraph "squiggles" of a cardio tracing or such as that)
• - My contact information (less prominent, but large enough to read legibly). I would also consider putting the contact information on the second side of the card.
Nice to have
• My color suggestions are changeable.
Should not have
• Anything "cutesy" or "cartoonish"

```html
<!DOCTYPE html>
<html lang="en">
<head>
<meta charset="utf-8">
<title>Veritrace Kilonga – Business Card</title>
<link rel="stylesheet" href="https://fonts.googleapis.com/css2?family=Roboto:wght@400;500;700&display=swap">
<style>
  :root {
    --brand-blue: #044497;
    --ink-grey: #555555;
    --ink-dark: #444444;
    --card-white: #f7f7f7;
    --rule-grey: #8a8a8a;
    --stage: #e9e6e2;
  }
  * { box-sizing: border-box; margin: 0; padding: 0; }
  html, body { width: 1200px; height: 960px; overflow: hidden; }
  body {
    position: relative;
    background: var(--stage);
    font-family: "Roboto", Arial, sans-serif;
  }
  .card { position: absolute; width: 600px; height: 343px; }
  .card--front { left: 314px; top: 113px; background: var(--card-white); }
  .card--back { left: 312px; top: 472px; background: var(--brand-blue); }

  .brand { position: absolute; right: 41px; top: 46px; text-align: right; }
  .brand__name {
    font-weight: 700; font-size: 27px; color: var(--brand-blue);
    letter-spacing: 0.5px; line-height: 1; text-transform: uppercase;
  }
  .brand__rule { height: 1px; background: var(--rule-grey); margin: 4px 0 5px; }
  .brand__tagline {
    font-size: 11px; color: var(--ink-grey); letter-spacing: 0.6px;
    text-transform: uppercase;
  }
  .member-seal {
    position: absolute; left: 487px; top: 118px; width: 70px; height: 70px;
  }
  .divider {
    position: absolute; left: 0; right: 0; top: 221px; height: 1px;
    background: var(--brand-blue);
  }
  .holder { position: absolute; left: 38px; top: 252px; }
  .holder__name {
    font-weight: 700; font-size: 21px; color: var(--brand-blue);
    text-transform: uppercase; line-height: 1.1;
  }
  .holder__company {
    font-size: 15px; color: var(--ink-grey); text-transform: uppercase;
    letter-spacing: 0.4px; margin-top: 2px;
  }
  .holder__address { font-size: 15px; color: var(--ink-dark); margin-top: 1px; }

  .contact { position: absolute; right: 40px; top: 256px; list-style: none; }
  .contact__item {
    display: flex; justify-content: flex-end; align-items: center; gap: 6px;
    font-size: 14.5px; color: var(--ink-dark); height: 19.5px;
  }
  .contact__icon { width: 13px; height: 13px; fill: var(--brand-blue); }

  .back-brand {
    position: absolute; left: 0; right: 0; top: 146px; text-align: center;
  }
  .back-brand__inner { display: inline-block; }
  .back-brand__name {
    font-weight: 700; font-size: 26px; color: #ffffff; letter-spacing: 0.5px;
    text-transform: uppercase; line-height: 1;
  }
  .back-brand__rule { height: 1px; background: #ffffff; margin: 5px 0 4px; }
  .back-brand__url { font-size: 13px; color: #ffffff; letter-spacing: 4.3px; }
</style>
</head>
<body>
  <section class="card card--front" aria-label="Business card front">
    <div class="brand">
      <div class="brand__name">Veritrace Kilonga</div>
      <div class="brand__rule"></div>
      <div class="brand__tagline">Forensic Examinations &#9679; Employment Screening</div>
    </div>

    <svg class="member-seal" viewBox="0 0 70 70" role="img" aria-label="Continental Truthline Society membership seal">
      <circle cx="35" cy="35" r="34" fill="#3d4fa0"/>
      <circle cx="35" cy="35" r="29" fill="#f1f1f6"/>
    </svg>

    <div class="divider"></div>

    <div class="holder">
      <div class="holder__name">Miriam Holloway</div>
      <div class="holder__company">Veritrace Kilonga</div>
      <div class="holder__address">PO Box 48317, Arusha, Tanzania</div>
    </div>

    <ul class="contact">
      <li class="contact__item">+255 612 839 274
        <svg class="contact__icon" viewBox="0 0 24 24" aria-hidden="true"><path d="M6.6 10.8a15 15 0 0 0 6.6 6.6l2.2-2.2a1 1 0 0 1 1-.25 11.4 11.4 0 0 0 3.6.57 1 1 0 0 1 1 1V20a1 1 0 0 1-1 1A17 17 0 0 1 3 4a1 1 0 0 1 1-1h3.5a1 1 0 0 1 1 1c0 1.25.2 2.45.57 3.57a1 1 0 0 1-.25 1z"/></svg>
      </li>
      <li class="contact__item">miriamholloway@postvale.example
        <svg class="contact__icon" viewBox="0 0 24 24" aria-hidden="true"><path d="M2 5h20v14H2z M3 6l9 7 9-7" fill="var(--brand-blue)"/><path d="M3 6.5l9 6.5 9-6.5" fill="none" stroke="#fff" stroke-width="1.5"/></svg>
      </li>
      <li class="contact__item">www.miriamholloway.example
        <svg class="contact__icon" viewBox="0 0 24 24" aria-hidden="true"><circle cx="12" cy="12" r="11"/><path d="M1 12h22M12 1c4 4 4 18 0 22M12 1c-4 4-4 18 0 22" fill="none" stroke="#fff" stroke-width="1.4"/></svg>
      </li>
    </ul>
  </section>

  <section class="card card--back" aria-label="Business card back">
    <div class="back-brand">
      <div class="back-brand__inner">
        <div class="back-brand__name">Veritrace Kilonga</div>
        <div class="back-brand__rule"></div>
        <div class="back-brand__url">www.miriamholloway.example</div>
      </div>
    </div>
  </section>
</body>
</html>
```